Webbanner-Design
Verkauf von Pools und Zubehör
Es soll ein Banner für unseren Shop sein für eine Aktion, dass Holzpools jetzt sofort lieferbar sind Text:
Verschönern Sie doch Ihren Garten: Holzpools sofort lieferbar!
Unseren Shop finden Sie unter www.brunnkarst17.de
Fotos können von unserer Seite www.brunnkarst17-gallery.de verwendet werden
Das angefügte Bild sollte ebenfalls dabei sein. Hintergrund: die Leute sollen wegen Corona zu Hause bleiben und haben Zeit, daher sind unsere sofort lieferbaren Pools jetzt natürlich gut. Ich bin auch für abweichende Texte offen.

```html
<!DOCTYPE html>
<html lang="de">
<head>
<meta charset="utf-8">
<title>Brunnkarst17 – Holzpools sofort lieferbar</title>
<link href="https://fonts.googleapis.com/css2?family=Open+Sans:wght@400;600;700;800&display=swap" rel="stylesheet">
<style>
:root{
  --cyan:#00b4e6;
  --navy:#0d0f7a;
  --banner-cyan:#1fa9ee;
  --badge:#103f94;
  --text:#333;
  --muted:#555;
  --line:#e5e5e5;
  --page:#eeeeee;
  --water-a:#2f9fd8;
  --water-b:#7fd0f2;
}
*{box-sizing:border-box;margin:0;padding:0}
html,body{width:1200px;height:1023px;overflow:hidden}
body{font-family:"Open Sans",sans-serif;color:var(--text);background:var(--page);position:relative}
.water{position:absolute;left:0;top:0;width:1200px;height:577px;background:linear-gradient(135deg,var(--water-a),var(--water-b) 40%,var(--water-a) 70%,var(--water-b))}
.page{position:absolute;left:99px;top:0;width:1002px;height:1023px;background:#fff}
.topbar{position:absolute;left:0;top:0;width:1002px;height:32px;background:var(--cyan);color:#fff;font-size:13px}
.topbar span{position:absolute;top:8px;display:flex;align-items:center;gap:4px}
.topbar svg{width:11px;height:11px}
.meta-nav{position:absolute;right:26px;top:43px;font-size:11px;display:flex}
.meta-nav a{color:var(--text);text-decoration:none;padding:0 5px;border-left:1px solid #ddd}
.meta-nav a:first-child{border-left:0}
.brand{position:absolute;left:22px;top:88px;display:flex;align-items:center;gap:8px;font-size:26px;font-weight:700;color:var(--badge)}
.brand i{width:14px;height:14px;border-radius:50%;background:var(--cyan);display:block}
.search{position:absolute;left:548px;top:90px;width:222px;height:30px;border:1px solid #ccc;border-radius:3px;font-size:13px;color:#999;padding:6px 11px}
.search b{position:absolute;right:0;top:0;width:37px;height:28px;border-left:1px solid #ccc;background:#f7f7f7;display:flex;align-items:center;justify-content:center}
.account{position:absolute;left:795px;top:97px;font-size:13px}
.cart{position:absolute;left:905px;top:97px;font-size:13px}
.menu{position:absolute;left:0;top:175px;width:1002px;height:44px;border-top:2px solid var(--line);border-bottom:2px solid var(--line);display:flex;align-items:center;padding-left:24px;gap:21px;font-size:13.5px;color:var(--muted)}
.caret{display:inline-block;border-left:3.5px solid transparent;border-right:3.5px solid transparent;border-top:4px solid var(--muted);vertical-align:middle;margin-left:2px}
.banner{position:absolute;left:20px;top:241px;width:962px;height:324px;background:var(--navy);overflow:hidden}
.banner-photo{position:absolute;left:420px;top:0;width:542px;height:324px;background:linear-gradient(160deg,#3a4a3a,#1a8ff0 30%,#0f6fd8 60%,#b0704a 80%,#4a5a3a)}
.banner svg.cut{position:absolute;left:0;top:0}
.headline{position:absolute;left:42px;top:60px;color:#fff;font-weight:700;font-size:26px;line-height:32px}
.offer{position:absolute;left:41px;top:140px;color:var(--banner-cyan);font-weight:800;font-size:44px;line-height:42px}
.badge{position:absolute;left:763px;top:126px;width:191px;height:191px;background:var(--badge);padding:58px 0 0 45px;font-weight:800;font-size:29px;line-height:25px;letter-spacing:-1px}
.badge .w{color:#fff}.badge .c{color:var(--banner-cyan)}
.dots{position:absolute;left:452px;top:592px;display:flex;gap:17px;align-items:center}
.dots i{width:6px;height:6px;border-radius:50%;background:#444;display:block}
.dots i.on{width:10px;height:10px;background:#fff;border:2px solid #444}
.rule{position:absolute;left:22px;top:642px;width:958px;border-top:1px solid var(--line)}
.section-title{position:absolute;left:22px;top:657px;font-size:21px;font-weight:400}
.cat{position:absolute;top:756px;width:264px;text-align:center;font-size:13px}
.cat .img{height:198px}
.cat p{margin-top:41px}
</style>
</head>
<body>
<div class="water" role="img" aria-label="Wasseroberfläche eines Pools als Seitenhintergrund"></div>
<div class="page">
  <div class="topbar">
    <span style="left:95px"><svg viewBox="0 0 12 12"><path d="M2 1l2 0 1 3-1.5 1a7 7 0 0 0 3.5 3.5l1-1.5 3 1 0 2c0 1-1 1-1 1A10 10 0 0 1 1 2s0-1 1-1z" fill="#fff"/></svg>+49 (0) 4412 / 318 760 2</span>
    <span style="left:334px"><svg viewBox="0 0 12 12"><rect width="12" height="12" rx="2" fill="#fff"/><path d="M3 6l2 2 4-4" stroke="#00b4e6" stroke-width="1.8" fill="none"/></svg>persönliche Beratung</span>
    <span style="left:580px"><svg viewBox="0 0 12 12"><rect width="12" height="12" rx="2" fill="#fff"/><path d="M3 6l2 2 4-4" stroke="#00b4e6" stroke-width="1.8" fill="none"/></svg>sicher Einkaufen</span>
    <span style="left:812px"><svg viewBox="0 0 12 12"><circle cx="6" cy="6" r="6" fill="#fff"/><path d="M3 6h5M6 3.5L8.5 6 6 8.5" stroke="#00b4e6" stroke-width="1.6" fill="none"/></svg>Brunnkarst-Galerie</span>
  </div>
  <nav class="meta-nav"><a>Startseite</a><a>Mein Konto</a><a>Kontakt</a><a>Unsere Partner</a><a>Bildergalerie</a><a>Wir über uns</a><a>News</a></nav>
  <div class="brand"><i></i>Brunnkarst17</div>
  <div class="search">Suchen<b><svg width="15" height="15" viewBox="0 0 15 15"><circle cx="6" cy="6" r="4.5" stroke="#00b4e6" stroke-width="2" fill="none"/><path d="M9.5 9.5l4 4" stroke="#00b4e6" stroke-width="2.2"/></svg></b></div>
  <div class="account">👤 Anmelden <span class="caret"></span></div>
  <div class="cart">🛒 0,00 € <span class="caret"></span></div>
  <div class="menu"><span>Sonderangebote</span><span>Pool &amp; Zubehör<i class="caret"></i></span><span>Sauna<i class="caret"></i></span><span>Infrarot<i class="caret"></i></span><span>Holzbadewannen</span></div>

  <section class="banner">
    <div class="banner-photo" role="img" aria-label="Achteckiger Holzpool mit blauem Wasser und Leiter im Garten"></div>
    <svg class="cut" width="962" height="324" viewBox="0 0 962 324">
      <path d="M0 0H434L370 150Q358 175 372 200L430 324H0Z" fill="#0d0f7a"/>
      <path d="M434 0H448L385 150Q374 175 387 200L443 324H430L372 200Q358 175 370 150Z" fill="#fff"/>
    </svg>
    <div class="headline">VERSCHÖNERN SIE<br>DOCH IHREN GARTEN</div>
    <div class="offer">HOLZPOOLS<br>SOFORT<br>LIEFERBAR!</div>
    <div class="badge"><span class="w">STAY<br>HOME</span><br><span class="c">SAVE<br>LIVES</span></div>
  </section>
  <div class="dots"><i></i><i class="on"></i><i></i><i></i><i></i></div>

  <div class="rule"></div>
  <h2 class="section-title">Unsere TOP-Kategorien</h2>
  <div class="cat" style="left:42px"><div class="img" role="img" aria-label="Holzpool mit Terrasse im Garten" style="background:linear-gradient(180deg,#6fa0d8,#3c6a2e 40%,#b08a5a 65%,#4e8a30)"></div><p>Holzpools</p></div>
  <div class="cat" style="left:369px"><div class="img" role="img" aria-label="Blaue Poolabdeckung auf gepflastertem Rand" style="background:linear-gradient(90deg,#777,#1a8fe0 20%,#1a8fe0 80%,#777)"></div><p>Poolabdeckungen</p></div>
  <div class="cat" style="left:697px"><div class="img" role="img" aria-label="Pool mit Rollladenabdeckung auf Natursteinterrasse" style="background:linear-gradient(160deg,#2e3a2a,#a8c8e0 35%,#1a6fd0 60%,#8a8a8a)"></div><p>Oberflur</p></div>
</div>
</body>
</html>
```